Business Card Design for BrightvaleMedia.com

--I need a business card design for my company BrightvaleMedia.com

I have attached my logo...I want the brightvale media logo on the front of the business card, and then I want The Quillstone Chief on the back of it with my information.

I would like to see a light colored background as well as a dark colored background

FRONT:
BRIGHTVALE MEDIA LOGO
248 N. Larkmoor
3rd Floor
San Diego CA 92173
www.BrightvaleMedia.com

Advanced Website & App Development
Websites, Apps, Online Voucher Systems

Leading Edge Marketing Services
SMS, VB, SMM, SEM,

BACK:
QUILLSTONE CHIEF LOGO
Dorian Pelletta
The Quillstone Chief
Call Or Text: 619-555-0148
Dorian@QuillstoneChief.example
www.QuillstoneChief.example

Target Market(s)

small business owners

Industry/Entity Type

Business Consultant

Contact Information for Business Card

FRONT:
BRIGHTVALE MEDIA LOGO
248 N. Larkmoor
3rd Floor
San Diego CA 92173
www.BrightvaleMedia.com

SMS, VB, SMM, SEM,

BACK:
QUILLSTONE CHIEF LOGO
Dorian Pelletta
The Quillstone Chief
Dorian@QuillstoneChief.example
www.QuillstoneChief.example

Requirements
Must have
• add this quote on it somewhere, anywhere,preferrably on back
• "The Fastest Way To Success Is To Take Action”
• — Dorian Pelletta, Quillstone Chief
Nice to have
• open
Should not have
• red

```html
<!DOCTYPE html>
<html lang="en">
<head>
<meta charset="utf-8">
<title>Brightvale Media Business Card</title>
<link rel="stylesheet" href="https://fonts.googleapis.com/css2?family=Source+Sans+3:wght@400;600&display=swap">
<style>
  :root {
    --backdrop: #ecebe9;
    --card-white: #ffffff;
    --brand-blue: #1170aa;
    --text-grey: #555a5e;
    --text-light: #ffffff;
    --text-soft: rgba(255,255,255,0.85);
  }
  * { margin: 0; padding: 0; box-sizing: border-box; }
  html, body {
    width: 1200px;
    height: 900px;
    overflow: hidden;
    background: var(--backdrop);
    font-family: "Source Sans 3", "Myriad Pro", Arial, sans-serif;
  }
  .canvas { position: relative; width: 1200px; height: 900px; }

  .card {
    position: absolute;
    background: var(--card-white);
    overflow: hidden;
    box-shadow: 0 6px 18px rgba(0,0,0,0.18);
  }
  .card-back  { left: 237px; top: 60px;  width: 556px; height: 345px; }
  .card-front { left: 459px; top: 518px; width: 560px; height: 342px; }

  .card-top {
    position: relative;
    display: flex;
    flex-direction: column;
    align-items: center;
  }
  .card-back .card-top  { height: 187px; justify-content: center; }
  .card-front .card-top { height: 187px; justify-content: flex-end; padding-bottom: 22px; }

  .brand-name {
    color: var(--brand-blue);
    font-weight: 400;
    text-transform: uppercase;
    white-space: nowrap;
    line-height: 1;
  }
  .card-back .brand-name  { font-size: 40px; letter-spacing: 0.1em; padding-left: 0.1em; }
  .card-front .brand-name { font-size: 42px; letter-spacing: 0.12em; padding-left: 0.12em; margin-bottom: 42px; }

  .address { font-size: 17px; color: var(--text-grey); }

  .card-band {
    position: absolute;
    left: 0; right: 0; bottom: 0;
    background: var(--brand-blue);
    color: var(--text-light);
  }
  .card-back .card-band  { height: 158px; }
  .card-front .card-band { height: 155px; }

  .person {
    position: absolute;
    left: 0; width: 227px; top: 56px;
    text-align: right;
  }
  .person-name  { font-size: 19px; font-weight: 600; line-height: 1.2; }
  .person-title { font-size: 16.5px; line-height: 1.3; }

  .contact-list {
    position: absolute;
    left: 256px; top: 46px;
    list-style: none;
    font-size: 16.5px;
    line-height: 20px;
  }
  .contact-list li { display: flex; align-items: center; gap: 8px; }
  .contact-list svg { width: 12px; height: 12px; fill: var(--text-light); flex: none; }

  .quote {
    position: absolute;
    left: 0; right: 0; top: 121px;
    text-align: center;
    font-size: 13px;
    line-height: 16px;
    color: var(--text-soft);
  }

  .services {
    text-align: center;
    font-size: 17px;
    line-height: 20px;
    padding-top: 25px;
  }
  .services p + p { margin-top: 13px; }
  .services .website { margin-top: 15px; }
</style>
</head>
<body>
<main class="canvas">

  <section class="card card-back" aria-label="Card back">
    <div class="card-top">
      <div class="brand-name">Quillstone Chief</div>
    </div>
    <div class="card-band">
      <div class="person">
        <div class="person-name">Dorian Pelletta</div>
        <div class="person-title">The Quillstone Chief</div>
      </div>
      <ul class="contact-list">
        <li>
          <svg viewBox="0 0 24 24" aria-hidden="true"><path d="M6.6 10.8a15 15 0 0 0 6.6 6.6l2.2-2.2a1 1 0 0 1 1-.25 11.4 11.4 0 0 0 3.6.57 1 1 0 0 1 1 1V20a1 1 0 0 1-1 1A17 17 0 0 1 3 4a1 1 0 0 1 1-1h3.5a1 1 0 0 1 1 1c0 1.25.2 2.45.57 3.57a1 1 0 0 1-.25 1z"/></svg>
          619-555-0148
        </li>
        <li>
          <svg viewBox="0 0 24 24" aria-hidden="true"><path d="M2 5h20v14H2z M3 6l9 7 9-7" stroke="#1170aa" stroke-width="1.5"/></svg>
          Dorian@QuillstoneChief.example
        </li>
        <li>
          <svg viewBox="0 0 24 24" aria-hidden="true"><circle cx="12" cy="12" r="10"/></svg>
          www.QuillstoneChief.example
        </li>
      </ul>
      <p class="quote">“The Fastest Way To Success Is To Take Action” — Dorian Pelletta, Quillstone Chief</p>
    </div>
  </section>

  <section class="card card-front" aria-label="Card front">
    <div class="card-top">
      <div class="brand-name">Brightvale Media</div>
      <div class="address">248 N. Larkmoor 3rd Floor, San Diego CA 92173</div>
    </div>
    <div class="card-band">
      <div class="services">
        <p>Advanced Website &amp; App Development | Websites | Apps<br>Online Voucher Systems</p>
        <p>Leading Edge Marketing Services | SMS | VB | SMM | SEM,</p>
        <p class="website">www.BrightvaleMedia.com</p>
      </div>
    </div>
  </section>

</main>
</body>
</html>
```